Corporate Business Card

Very professional, Modern, Not to busy, include phone address email, website
(541) 617-4930, 18761 52nd Avenue S, Brenton, OR 98047, martin@plumlinegroup.com, varkoworks.com

Target Market(s)

Manufacturing

Industry/Entity Type

Aero, machining, manufacturing, Off road racing

Contact Information for Business Card

Phone, address email, website

```html
<!DOCTYPE html>
<html lang="en">
<head>
<meta charset="utf-8">
<title>Varko Works — Business Card</title>
<link rel="stylesheet" href="https://fonts.googleapis.com/css2?family=Poppins:wght@600;700&display=swap">
<style>
  :root {
    --navy: #16326b;
    --red: #d1202a;
    --white: #ffffff;
    --backdrop: #e4e4e4;
  }
  * { margin: 0; padding: 0; box-sizing: border-box; }
  html, body {
    width: 1200px; height: 1200px; overflow: hidden;
    background: var(--backdrop);
    font-family: "Poppins", sans-serif;
  }
  .stage { position: relative; width: 1200px; height: 1200px; }
  .card {
    position: absolute; top: 215px;
    width: 440px; height: 770px;
    border-radius: 26px; overflow: hidden;
    background: var(--white);
  }
  .card--front { left: 130px; }
  .card--back { left: 630px; }
  .card__art { position: absolute; inset: 0; width: 100%; height: 100%; display: block; }
  .brand {
    position: absolute; left: 0; right: 0;
    display: flex; align-items: center; justify-content: center; gap: 12px;
    transform: translateY(-50%);
  }
  .card--front .brand { top: 320px; }
  .card--back .brand { top: 240px; }
  .brand__mark { width: 18px; height: 18px; background: var(--red); }
  .brand__name {
    font-weight: 700; font-size: 44px; letter-spacing: 0.5px;
    color: var(--navy); line-height: 1;
  }
  .pattern-fill {
    position: absolute; left: 0; right: 0; top: 434px; height: 300px;
    background: linear-gradient(180deg, #1a3872, #16326b);
  }
  .contact {
    position: absolute; left: 0; right: 0; top: 510px;
    list-style: none; text-align: center;
    color: var(--white); font-weight: 600; font-size: 19px; line-height: 36px;
    letter-spacing: 0.3px;
  }
</style>
</head>
<body>
<main class="stage">

  <section class="card card--front" aria-label="Card front">
    <svg class="card__art" viewBox="0 0 662 1158" preserveAspectRatio="none" aria-hidden="true">
      <polygon points="0,0 120,0 48,57 0,57" fill="var(--red)"/>
      <polygon points="662,0 542,0 614,57 662,57" fill="var(--red)"/>
      <polyline points="0,133 118,133 290,0" fill="none" stroke="var(--navy)" stroke-width="4"/>
      <polyline points="372,0 545,133 662,133" fill="none" stroke="var(--navy)" stroke-width="4"/>
      <polyline points="0,603 188,603 240,653" fill="none" stroke="var(--navy)" stroke-width="4"/>
      <polyline points="422,653 474,603 662,603" fill="none" stroke="var(--navy)" stroke-width="4"/>
      <rect x="0" y="653" width="662" height="505" fill="var(--navy)"/>
      <rect x="0" y="1114" width="662" height="5" fill="var(--white)"/>
    </svg>
    <div class="pattern-fill" role="img" aria-label="Faint repeating brand-name pattern in navy"></div>
    <div class="brand">
      <span class="brand__mark"></span>
      <span class="brand__name">Varko Works</span>
    </div>
  </section>

  <section class="card card--back" aria-label="Card back">
    <svg class="card__art" viewBox="0 0 664 1158" preserveAspectRatio="none" aria-hidden="true">
      <polyline points="0,48 184,48 234,0" fill="none" stroke="var(--navy)" stroke-width="4"/>
      <polyline points="430,0 480,48 664,48" fill="none" stroke="var(--navy)" stroke-width="4"/>
      <polyline points="0,116 203,116 333,-14 463,116 664,116" fill="none" stroke="var(--red)" stroke-width="30"/>
      <line x1="0" y1="600" x2="664" y2="600" stroke="var(--red)" stroke-width="2"/>
      <g class="icon-row" fill="var(--red)">
        <circle cx="196" cy="598" r="27"/>
        <circle cx="285" cy="598" r="27"/>
        <circle cx="376" cy="598" r="27"/>
        <circle cx="466" cy="598" r="27"/>
      </g>
      <g fill="none" stroke="var(--white)" stroke-width="2.5" stroke-linecap="round" stroke-linejoin="round">
        <path d="M184,586 l6,-3 5,9 -4,3 q3,7 9,11 l3,-4 9,5 -3,6 q-14,2 -25,-27z"/>
        <path d="M200,584 q6,1 8,8 M202,579 q10,2 12,12"/>
        <rect x="272" y="588" width="26" height="19" rx="2"/>
        <path d="M272,588 l13,11 13,-11 M272,607 l10,-9 M298,607 l-10,-9"/>
        <path d="M376,614 q-12,-13 -12,-22 a12,12 0 0 1 24,0 q0,9 -12,22z"/>
        <circle cx="376" cy="592" r="4"/>
        <circle cx="466" cy="598" r="14"/>
        <ellipse cx="466" cy="598" rx="6" ry="14"/>
        <path d="M452,598 h28 M455,590 h22 M455,606 h22"/>
      </g>
      <polygon points="0,672 226,672 245,653 419,653 438,672 664,672 664,1077 440,1077 419,1098 245,1098 224,1077 0,1077" fill="var(--navy)"/>
      <polyline points="0,1111 190,1111 237,1158" fill="none" stroke="var(--navy)" stroke-width="4"/>
      <polyline points="427,1158 474,1111 664,1111" fill="none" stroke="var(--navy)" stroke-width="4"/>
    </svg>
    <div class="brand">
      <span class="brand__mark"></span>
      <span class="brand__name">Varko Works</span>
    </div>
    <ul class="contact">
      <li>varkoworks.com</li>
      <li>(541) 617-4930, 18761</li>
      <li>52nd Avenue S, Brenton, OR 98047</li>
      <li>martin@plumlinegroup.com</li>
    </ul>
  </section>

</main>
</body>
</html>
```